Yacht, Boats, Watersports company needs a redesign of business card

Hello Designers!
We are a Boat dealership company that sells fun in the water, we sell boats, Yachts, Kayaks and also yacht WaterSport toys. We are looking to redesign our business cards in to something a little bit more sophisticated. in a way that we can make better use of our company colors. I'm attaching a zipped file containing the company 3 sets of company logo which one is an horizontal another one is a vertical and also a chromed 3d logo. Also is included two set of business cards that we use and also some designs that i think it's interesting. We use PMS 2026c Orange and PMS 7687C Blue. I would like to see at least two different options with the orange as accent and also using blue as an accent color. It's really important for the business cards to have a font option and size that is legible to most people. Our current website is wwww.coralpennant.com. Please visit if you want to have a better feeling of the Boat dealership
You can send Single sided or double side options. We are now using single sided but we may be open for a double side option if we really like the design.
Target Market(s)
Marine, boat sales, yacht sales, water toys sales/
Contact Information for Business Card
Name: Dale Whitcombe
Address: 212 North Fenwick Lane,
Gull Harbor, FL 30917
Phone: 555-731-8842
Fax: 555:731-8843
Cell: 555-382-1490
Email: dw@coralpennant.com
Website: coralpennant.com
Requirements
Must have
- the current information of the business card provided.
logo
use the PMS Colors
Nice to have
- a touch of elegance and sophistication but simple
Should not have
- should not have any typography that is hard to read, the card should be simple but yet sophisticated.

```html
<!DOCTYPE html>
<html lang="en">
<head>
<meta charset="utf-8">
<title>Coral Pennant — Business Card</title>
<link rel="stylesheet" href="https://fonts.googleapis.com/css2?family=Krona+One&family=Open+Sans:wght@400;600&display=swap">
<style>
  :root {
    --brand-blue: #16467a;
    --brand-orange: #ef6530;
    --ink: #2b2b2b;
    --paper: #ffffff;
    --backdrop: #1d1e21;
  }
  * { box-sizing: border-box; margin: 0; padding: 0; }
  html, body { width: 1200px; height: 900px; overflow: hidden; }
  body {
    background: var(--backdrop);
    display: flex; flex-direction: column; align-items: center; justify-content: center;
    gap: 40px;
    font-family: "Open Sans", Arial, sans-serif;
  }
  .card {
    width: 680px; height: 388px; border-radius: 26px; position: relative; overflow: hidden;
    box-shadow: 0 12px 30px rgba(0,0,0,.45);
  }
  .card-front { background: var(--paper); }
  .card-back {
    background: var(--brand-blue);
    display: flex; align-items: center; justify-content: center;
  }
  .brand { display: flex; align-items: center; gap: 14px; }
  .brand-ring { border-radius: 50%; border: 5px solid var(--brand-orange); flex: none; }
  .brand-name {
    font-family: "Krona One", Arial, sans-serif; text-transform: uppercase; letter-spacing: 1px;
    white-space: nowrap;
  }
  .card-back .brand-ring { width: 84px; height: 84px; border-width: 8px; }
  .card-back .brand-name { color: var(--paper); font-size: 34px; }
  .card-front .brand { position: absolute; left: 150px; top: 44px; }
  .card-front .brand-ring { width: 46px; height: 46px; }
  .card-front .brand-name { color: var(--brand-blue); font-size: 20px; }
  .holder { position: absolute; left: 60px; top: 112px; }
  .holder-name {
    font-family: "Krona One", Arial, sans-serif; color: var(--brand-blue);
    font-size: 25px; text-transform: uppercase; letter-spacing: 1px; margin-bottom: 12px;
    white-space: nowrap;
  }
  .address { color: var(--ink); font-size: 16px; line-height: 1.35; margin-bottom: 6px; }
  .contact-list { list-style: none; }
  .contact-list li {
    display: flex; align-items: center; gap: 9px; color: var(--ink); font-size: 16px; line-height: 1.45;
    white-space: nowrap;
  }
  .contact-list svg { width: 13px; height: 13px; flex: none; fill: none; stroke: var(--brand-orange); stroke-width: 2; }
  .contact-list svg .solid { fill: var(--brand-orange); stroke: none; }
  .web-domain { color: var(--brand-blue); font-weight: 600; }
</style>
</head>
<body>
  <section class="card card-front">
    <div class="brand">
      <span class="brand-ring"></span>
      <span class="brand-name">Coral Pennant</span>
    </div>
    <div class="holder">
      <h1 class="holder-name">Dale Whitcombe</h1>
      <p class="address">212 North Fenwick Lane,<br>Gull Harbor, FL 30917</p>
      <ul class="contact-list">
        <li><svg viewBox="0 0 14 14"><path class="solid" d="M3 1l2.5 3-1.5 1.5c.8 1.8 2 3 3.5 3.5L9 7.5l3 2.5-1.5 2.5C6 12 2 8 1.5 2.5z"/></svg><span>555-731-8842</span></li>
        <li><svg viewBox="0 0 14 14"><rect class="solid" x="3" y="1" width="8" height="4"/><rect class="solid" x="1" y="6" width="12" height="6" rx="1"/></svg><span>555:731-8843</span></li>
        <li><svg viewBox="0 0 14 14"><rect x="3.5" y="1" width="7" height="12" rx="1.5"/></svg><span>555-382-1490</span></li>
        <li><svg viewBox="0 0 14 14"><rect x="1" y="3" width="12" height="8"/><path d="M1 3l6 5 6-5"/></svg><span>dw@coralpennant.com</span></li>
        <li><svg viewBox="0 0 14 14"><circle cx="7" cy="7" r="5.5"/><path d="M1.5 7h11M7 1.5c-3 3.5-3 7.5 0 11M7 1.5c3 3.5 3 7.5 0 11"/></svg><span>www.<span class="web-domain">coralpennant</span>.com</span></li>
      </ul>
    </div>
  </section>

  <section class="card card-back">
    <div class="brand">
      <span class="brand-name">Coral Pennant</span>
      <span class="brand-ring"></span>
    </div>
  </section>
</body>
</html>
```